New bussiness card, using company logo.
Lionel Brisk
Manager/Director
Brisk Property Developments
Po Box 5347
Thuringowa Central
Qld
0491 638 205
lionel@briskpropertydevelopments
eye catching, vibrant colours, professional

```html
<!DOCTYPE html>
<html lang="en">
<head>
<meta charset="utf-8">
<title>Brisk Property Developments – Business Cards</title>
<link rel="stylesheet" href="https://fonts.googleapis.com/css2?family=PT+Sans:wght@400;700&display=swap">
<style>
  :root {
    --backdrop: #2b2724;
    --card-white: #ffffff;
    --brand-red: #e1262c;
    --brand-green: #7dc142;
    --green-light: #93c83e;
    --green-deep: #5cae3f;
    --ink: #222222;
    --ink-soft: #666666;
    --rule: #c9c9c9;
  }
  * { margin: 0; padding: 0; box-sizing: border-box; }
  html, body { width: 1200px; height: 721px; overflow: hidden; }
  body {
    background: var(--backdrop);
    font-family: "PT Sans", Arial, sans-serif;
    position: relative;
  }
  .card {
    position: absolute;
    width: 548px;
    height: 311px;
    overflow: hidden;
  }
  .card--contact { left: 41px; top: 37px; background: var(--card-white); }
  .card--brand { left: 614px; top: 37px; background: var(--card-white); }
  .card--red { left: 41px; top: 376px; height: 314px; background: var(--brand-red); }
  .card--green {
    left: 614px; top: 378px; height: 312px;
    background: linear-gradient(135deg, var(--green-light), var(--green-deep));
  }

  .wordmark {
    position: absolute;
    display: flex;
    align-items: center;
    gap: 10px;
    font-weight: 700;
    line-height: 1.05;
    text-transform: uppercase;
  }
  .wordmark__square { flex: none; background: var(--brand-green); }
  .wordmark--contact { left: 44px; top: 90px; width: 260px; color: var(--brand-red); font-size: 24px; }
  .wordmark--contact .wordmark__square { width: 22px; height: 22px; }
  .wordmark--brand { left: 94px; top: 100px; width: 370px; color: var(--brand-red); font-size: 36px; }
  .wordmark--brand .wordmark__square { width: 30px; height: 30px; }
  .wordmark--red { left: 84px; top: 118px; width: 400px; color: var(--card-white); font-size: 42px; }
  .wordmark--green { left: 70px; top: 140px; width: 410px; color: var(--card-white); font-size: 34px; justify-content: center; text-align: center; }

  .divider { position: absolute; left: 325px; top: 58px; width: 1px; height: 136px; background: var(--rule); }
  .contact { position: absolute; left: 347px; top: 66px; color: var(--ink); font-size: 14px; line-height: 19px; }
  .contact__name { color: var(--brand-red); font-weight: 700; font-size: 19px; line-height: 22px; }
  .contact__role { color: var(--ink-soft); font-size: 15px; }
  .contact__phone { margin-top: 20px; display: flex; align-items: center; gap: 6px; }
  .contact__address { margin-top: 10px; }

  .swoosh { position: absolute; left: 0; bottom: 0; width: 548px; height: 70px; }
  .email {
    position: absolute; left: 46px; bottom: 11px;
    color: var(--card-white); font-size: 14px; letter-spacing: 0.3px;
    display: flex; align-items: center; gap: 7px;
  }

  .web {
    position: absolute; left: 0; width: 100%;
    text-align: center; font-size: 16px; letter-spacing: 1.2px;
  }
  .card--brand .web { top: 270px; color: var(--ink); }
  .card--red .web { top: 272px; color: var(--card-white); }
  .card--green .web { top: 272px; color: var(--card-white); }
</style>
</head>
<body>

<section class="card card--contact">
  <div class="wordmark wordmark--contact"><span class="wordmark__square"></span><span>Brisk Property Developments</span></div>
  <div class="divider"></div>
  <div class="contact">
    <div class="contact__name">Lionel Brisk</div>
    <div class="contact__role">Manager/Director</div>
    <div class="contact__phone">
      <svg width="12" height="12" viewBox="0 0 12 12" aria-hidden="true">
        <circle cx="6" cy="6" r="5.3" fill="none" stroke="#7dc142" stroke-width="1.2"/>
        <path d="M4 3.2 L5 3 L5.6 4.6 L5 5.1 Q5.6 6.5 6.9 7 L7.4 6.4 L9 7 L8.8 8 Q6 8.4 4 4.2 Z" fill="#7dc142"/>
      </svg>
      <span>0491 638 205</span>
    </div>
    <div class="contact__address">Po Box 5347<br>Ashbridge Central , Nld</div>
  </div>
  <svg class="swoosh" viewBox="0 0 548 70" preserveAspectRatio="none" aria-hidden="true">
    <defs>
      <linearGradient id="swooshGreen" x1="0" x2="1" y1="0" y2="0">
        <stop offset="0" stop-color="#93c83e"/>
        <stop offset="1" stop-color="#5cae3f"/>
      </linearGradient>
    </defs>
    <path d="M0 18 Q260 -4 548 40 L548 70 L0 70 Z" fill="url(#swooshGreen)"/>
    <path d="M0 12 Q260 -10 548 36 L548 42 Q260 0 0 18 Z" fill="#e1262c"/>
  </svg>
  <div class="email">
    <svg width="11" height="9" viewBox="0 0 11 9" aria-hidden="true">
      <rect x="0.5" y="0.5" width="10" height="8" rx="1" fill="#fff"/>
      <path d="M1 1.5 L5.5 5 L10 1.5" fill="none" stroke="#7dc142" stroke-width="1"/>
    </svg>
    <span>lionel@briskpropertydevelopments.com</span>
  </div>
</section>

<section class="card card--brand">
  <div class="wordmark wordmark--brand"><span class="wordmark__square"></span><span>Brisk Property Developments</span></div>
  <div class="web">www.briskpropertydevelopments.com</div>
</section>

<section class="card card--red">
  <div class="wordmark wordmark--red"><span>Brisk Property Developments</span></div>
  <div class="web">www.briskpropertydevelopments.com</div>
</section>

<section class="card card--green">
  <div class="wordmark wordmark--green"><span>Brisk Property Developments</span></div>
  <div class="web">www.briskpropertydevelopments.com</div>
</section>

</body>
</html>
```